Coffeeshop menu for filter tip

We want to have a cannabis (coffeeshop) menu in the size 25mm wide x 60mm wide. Some examples attached.

it must have the following text:
Menu

WEED p/g
Oblivane €16
Cloudplum €14
Tide Runner €14
Quincefig €16
Mega Marsh €14
Grey Heron €14

HASH p/g
Tashar Amber €12
Pebble Frost€11
Lime Dunes €14
Ash Petal €10

Target Market(s)

tourist in Amsterdam

Requirements
Nice to have
• cannabis sign leaf
• No Cigarettes allowed symbol

```html
<!DOCTYPE html>
<html lang="en">
<head>
<meta charset="utf-8">
<title>Amsterdam Menu</title>
<link rel="stylesheet" href="https://fonts.googleapis.com/css2?family=Arimo:wght@400;700&display=swap">
<style>
  :root {
    --ink: #030506;
    --paper: #ffffff;
    --amber: #f9a81b;
    --signal-red: #e0202a;
  }
  html, body {
    margin: 0;
    padding: 0;
    width: 1200px;
    height: 2878px;
    overflow: hidden;
    background: var(--ink);
  }
  .menu-card {
    position: relative;
    width: 1200px;
    height: 2878px;
    background: var(--ink);
    color: var(--paper);
    font-family: "Arimo", Arial, sans-serif;
  }
  .city, .title, .section-name, .unit, .note {
    position: absolute;
    margin: 0;
    line-height: 1;
    white-space: nowrap;
  }
  .city {
    top: 89px;
    left: 0;
    width: 1200px;
    text-align: center;
    font-size: 98px;
    font-weight: 700;
    letter-spacing: 0.4em;
    padding-left: 0.4em;
    box-sizing: border-box;
  }
  .title {
    top: 218px;
    left: 0;
    width: 1200px;
    text-align: center;
    font-size: 158px;
    font-weight: 700;
    letter-spacing: 0.24em;
    padding-left: 0.24em;
    box-sizing: border-box;
  }
  .rule {
    position: absolute;
    left: 0;
    width: 1200px;
    height: 8px;
    background: var(--paper);
  }
  .section-name {
    left: 63px;
    font-size: 156px;
    font-weight: 700;
    letter-spacing: 0.1em;
    color: var(--amber);
  }
  .unit {
    right: 60px;
    font-size: 128px;
    font-weight: 700;
    color: var(--amber);
  }
  .price-list {
    position: absolute;
    left: 58px;
    right: 56px;
    margin: 0;
    padding: 0;
    list-style: none;
  }
  .price-list li {
    display: flex;
    justify-content: space-between;
    height: 143px;
    line-height: 143px;
    font-size: 123px;
    letter-spacing: 0.04em;
  }
  .price-list .price { letter-spacing: 0.06em; margin-right: -0.06em; }
  .weed-list { top: 694px; }
  .hash-list { top: 1823px; left: 62px; right: 45px; }
  .hash-list li { height: 144px; }
  .no-smoking {
    position: absolute;
    left: 78px;
    top: 2500px;
    width: 244px;
    height: 244px;
  }
  .note {
    left: 394px;
    top: 2584px;
    font-size: 98px;
    letter-spacing: 0.06em;
  }
</style>
</head>
<body>
<main class="menu-card">
  <p class="city">AMSTERDAM</p>
  <h1 class="title">MENU</h1>

  <div class="rule" style="top:450px"></div>
  <h2 class="section-name" style="top:494px">WEED</h2>
  <span class="unit" style="top:490px">p/g</span>
  <div class="rule" style="top:671px"></div>

  <ul class="price-list weed-list">
    <li><span class="name">Oblivane</span><span class="price">€16</span></li>
    <li><span class="name">Cloudplum</span><span class="price">€14</span></li>
    <li><span class="name">Tide Runner</span><span class="price">€14</span></li>
    <li><span class="name">Quincefig</span><span class="price">€16</span></li>
    <li><span class="name">Mega Marsh</span><span class="price">€14</span></li>
    <li><span class="name">Grey Heron</span><span class="price">€14</span></li>
  </ul>

  <div class="rule" style="top:1572px"></div>
  <h2 class="section-name" style="top:1603px">HASH</h2>
  <span class="unit" style="top:1607px">p/g</span>
  <div class="rule" style="top:1787px"></div>

  <ul class="price-list hash-list">
    <li><span class="name">Tashar Amber</span><span class="price">€12</span></li>
    <li><span class="name">Pebble Frost</span><span class="price">€11</span></li>
    <li><span class="name">Lime Dunes</span><span class="price">€14</span></li>
    <li><span class="name">Ash Petal</span><span class="price">€10</span></li>
  </ul>

  <svg class="no-smoking" viewBox="0 0 244 244" role="img" aria-label="No smoking sign">
    <circle cx="122" cy="122" r="111" fill="var(--paper)" stroke="var(--signal-red)" stroke-width="22"/>
    <rect x="38" y="136" width="134" height="26" fill="var(--ink)"/>
    <rect x="178" y="136" width="7" height="26" fill="var(--ink)"/>
    <rect x="190" y="136" width="7" height="26" fill="var(--ink)"/>
    <path d="M150 42 c-22 4 -22 30 -2 34 c22 5 40 14 38 46 M172 48 c-8 6 -4 14 6 18 c14 6 22 20 20 40"
          fill="none" stroke="var(--ink)" stroke-width="6" stroke-linecap="round"/>
    <line x1="44" y1="44" x2="200" y2="200" stroke="var(--signal-red)" stroke-width="22"/>
  </svg>
  <p class="note">No Cigarettes</p>
</main>
</body>
</html>
```